Velk Partners Building Business Cards

We need a business card that reflects our business as "Solar Experts" in San Diego. Browse our website www.velkpartners.example our License needs to be displayed as "CSLB# 3867140" our phone number is (619) 555-0187

Save thousands on your electric bills and increase the value of your home while helping to protect the environment. Our solar installation experts will help you design the system that's right for you, using only the highest quality equipment that will look great and give you ideal performance. Our goal is to make you energy independent, and get your electric bill to 0.

Paul Osterby
(619) 555-0187
paul@velkpartners.example

Target Market(s)

Home owners in san diego looking for solar

Industry/Entity Type

Solar Energy

Contact Information for Business Card

Paul Osterby
(619) 555-0187
paul@velkpartners.example

Font styles to use
Other font styles liked:
• Use our logo font

Requirements
Must have
• License needs to be displayed as "CSLB# 3867140" our phone number is (619) 555-0187
Nice to have
• Real images of rooftop home solar in san diego
Should not have
• our business address

```html
<!DOCTYPE html>
<html lang="en">
<head>
<meta charset="utf-8">
<title>Velk Partners Building – Business Cards</title>
<link rel="stylesheet" href="https://fonts.googleapis.com/css2?family=Open+Sans:wght@400;600;700&display=swap">
<style>
  :root {
    --navy: #1f3d7a;
    --sun: #f6ad1a;
    --white: #ffffff;
    --stage: #e9e7e4;
    --sky-light: #4a8ad6;
    --sky: #2f6fc2;
    --panel: #2a58a6;
    --panel-dark: #1b3a7c;
  }
  * { box-sizing: border-box; margin: 0; padding: 0; }
  html, body {
    width: 1200px;
    height: 900px;
    overflow: hidden;
    background: var(--stage);
    font-family: "Open Sans", Arial, sans-serif;
  }
  .canvas { position: relative; width: 1200px; height: 900px; }

  .card {
    position: absolute;
    overflow: hidden;
    box-shadow: 0 6px 18px rgba(0,0,0,0.18);
  }

  /* Front: contact card */
  .card-contact {
    left: 238px; top: 60px;
    width: 555px; height: 345px;
    background: var(--white);
  }
  .card-contact .swoosh { position: absolute; inset: 0; }

  .front-mark {
    position: absolute;
    left: 250px; top: 30px;
    width: 290px;
    display: flex;
    flex-direction: column;
    align-items: center;
    gap: 14px;
  }
  .front-mark .mark-circle {
    width: 120px; height: 120px;
    border-radius: 50%;
    background: var(--sun);
  }
  .front-mark .mark-name {
    color: var(--navy);
    font-weight: 700;
    font-size: 22px;
    line-height: 26px;
    white-space: nowrap;
  }

  .contact-name {
    position: absolute;
    left: 30px; top: 236px;
    color: var(--white);
    font-weight: 600;
    font-size: 21px;
  }
  .contact-lines {
    position: absolute;
    left: 30px; top: 284px;
    list-style: none;
    color: var(--white);
    font-size: 14px;
    line-height: 20px;
  }
  .contact-lines li { display: flex; align-items: center; gap: 8px; }
  .contact-lines svg { width: 11px; height: 11px; fill: var(--white); }
  .license {
    position: absolute;
    right: 34px; top: 303px;
    color: var(--white);
    font-size: 14px;
  }
  .license strong { font-weight: 600; font-size: 15px; }

  /* Back: brand card */
  .card-brand {
    left: 459px; top: 518px;
    width: 560px; height: 344px;
  }
  .panel-fill {
    position: absolute; inset: 0;
    background:
      linear-gradient(205deg, var(--sky-light) 0%, var(--sky) 38%, var(--panel) 52%, var(--panel-dark) 100%);
  }
  .brand-name {
    position: absolute;
    right: 26px; top: 48px;
    color: var(--white);
    font-weight: 600;
    font-size: 40px;
    line-height: 46px;
    text-align: right;
    letter-spacing: -0.5px;
    text-shadow: none;
  }
</style>
</head>
<body>
<main class="canvas">

  <section class="card card-contact">
    <svg class="swoosh" viewBox="0 0 555 345" preserveAspectRatio="none" aria-hidden="true">
      <path d="M0 0 L12 0 C60 150 150 250 290 258 C400 264 480 240 555 230 L555 345 L0 345 Z" fill="var(--navy)"/>
      <path d="M4 0 C52 150 142 246 290 253 C400 258 480 234 555 223" fill="none" stroke="var(--sun)" stroke-width="5"/>
    </svg>

    <div class="front-mark">
      <span class="mark-circle" aria-hidden="true"></span>
      <span class="mark-name">Velk Partners Building</span>
    </div>

    <h1 class="contact-name">Paul Osterby</h1>
    <ul class="contact-lines">
      <li>
        <svg viewBox="0 0 24 24"><path d="M6.6 10.8a15 15 0 0 0 6.6 6.6l2.2-2.2a1 1 0 0 1 1-.25 11.4 11.4 0 0 0 3.6.57 1 1 0 0 1 1 1V20a1 1 0 0 1-1 1A17 17 0 0 1 3 4a1 1 0 0 1 1-1h3.5a1 1 0 0 1 1 1c0 1.25.2 2.45.57 3.6a1 1 0 0 1-.25 1z"/></svg>
        (619) 555-0187
      </li>
      <li>
        <svg viewBox="0 0 24 24"><path d="M2 5h20v14H2z M2 5l10 8 10-8" stroke="var(--navy)" stroke-width="1.5"/></svg>
        paul@velkpartners.example
      </li>
    </ul>
    <p class="license"><strong>License:</strong> CSLB# 3867140</p>
  </section>

  <section class="card card-brand">
    <div class="panel-fill" role="img" aria-label="Photo of rooftop solar panels under a blue sky"></div>
    <p class="brand-name">Velk Partners<br>Building Inc</p>
  </section>

</main>
</body>
</html>
```